Marrowby Water Taxi and Transport Business Card

I need business cards for my new water taxi and freight transport business I have started here in Kodiak Alaska. Kodiak is a remote island in the middle of the gulf of Alaska. There are seven native villages around the island and Kodiak is the #2 fishing port in the United States. We also have the largest Coast Guard Base in the U.S. My company will be providing water taxi and freight transport logistics to the villages and many hunting and fishing lodges as well as remote properties around the island.

I would like a business card that isn't status quo, something that stands out, either in feel or appearance. I do like clean minimal designs but it needs to have the necessary contact info on it.

Target Market(s)

remote lodge / property owners, residents of the many villages around Kodiak and any one wanting to enjoy the great outdoors of Kodiak Alaska

Industry/Entity Type

Business

Contact Information for Business Card

I like clean simple designs that aren't cluttered but still provide the necessary information

Colors
0255a3
3277b5
33a4d5
9bcb3c
add136
fbed22
ffc214
f78f20
f37122

Requirements
Must have
• logo and contact info
• Captain Mason Elwick
• www.marrowbyferryline.com
• mason@marrowbyferryline.com

```html
<!DOCTYPE html>
<html lang="en">
<head>
<meta charset="utf-8">
<title>Marrowby Water Taxi and Transport – Business Card</title>
<link rel="stylesheet" href="https://fonts.googleapis.com/css2?family=Open+Sans:ital,wght@0,400;0,700;1,700&display=swap">
<style>
  :root {
    --navy: #0255a3;
    --mid-blue: #3277b5;
    --sky: #33a4d5;
    --card-dark: #2a2a2b;
    --card-light: #ffffff;
    --stage: #e9ecef;
    --ink-light: #ffffff;
  }
  * { box-sizing: border-box; margin: 0; padding: 0; }
  html, body { width: 1200px; height: 900px; overflow: hidden; }
  body {
    background: var(--stage);
    font-family: "Open Sans", Arial, sans-serif;
    position: relative;
  }
  .card {
    position: absolute;
    left: 270px;
    width: 660px;
    height: 377px;
    border-radius: 4px;
    box-shadow: 0 6px 18px rgba(0,0,0,.18);
    overflow: hidden;
  }
  .card-back { top: 48px; background: var(--card-dark); }
  .card-front { top: 465px; background: var(--card-light); }

  .wordmark {
    position: absolute;
    text-align: center;
    font-weight: 700;
    line-height: 1.05;
  }
  .wordmark .name { display: block; font-size: 52px; letter-spacing: 1px; }
  .wordmark .tagline { display: block; font-size: 22px; }
  .card-back .wordmark {
    color: var(--ink-light);
    left: 0; right: 0; top: 138px;
  }
  .card-front .wordmark {
    color: var(--navy);
    left: 345px; width: 290px; top: 120px;
  }
  .card-front .wordmark .name { font-size: 44px; }
  .card-front .wordmark .tagline { font-size: 19px; }

  .corner-mark { position: absolute; left: 0; top: 0; }
  .holder {
    position: absolute;
    left: 78px; top: 44px;
    font-size: 22px;
    font-weight: 700;
    font-style: italic;
    color: var(--sky);
  }
  .holder .surname { color: var(--navy); }

  .contact-list {
    position: absolute;
    left: 46px; top: 212px;
    list-style: none;
    font-size: 18px;
    color: var(--navy);
  }
  .contact-list li { display: flex; align-items: center; gap: 10px; line-height: 28px; }
  .contact-list svg { width: 14px; height: 14px; fill: var(--mid-blue); }

  .base-bands { position: absolute; left: 0; bottom: 0; }
</style>
</head>
<body>

  <section class="card card-back" aria-label="Card back">
    <div class="wordmark">
      <span class="name">MARROWBY</span>
      <span class="tagline">Water Taxi &amp; Transport</span>
    </div>
  </section>

  <section class="card card-front" aria-label="Card front">
    <svg class="corner-mark" width="80" height="60" viewBox="0 0 80 60" aria-hidden="true">
      <polygon points="0,0 62,0 22,52 0,52" fill="var(--navy)"/>
      <polygon points="30,52 70,2 70,52" fill="var(--sky)"/>
    </svg>

    <h1 class="holder">Captain Mason <span class="surname">Elwick</span></h1>

    <ul class="contact-list">
      <li>
        <svg viewBox="0 0 24 24" aria-hidden="true"><path d="M6.6 10.8a15.1 15.1 0 0 0 6.6 6.6l2.2-2.2a1 1 0 0 1 1-.25 11.4 11.4 0 0 0 3.6.57 1 1 0 0 1 1 1V20a1 1 0 0 1-1 1A17 17 0 0 1 3 4a1 1 0 0 1 1-1h3.5a1 1 0 0 1 1 1c0 1.25.2 2.45.57 3.6a1 1 0 0 1-.25 1z"/></svg>
        <span>mason@marrowbyferryline.com</span>
      </li>
      <li>
        <svg viewBox="0 0 24 24" aria-hidden="true"><path d="M2 5h20v14H2z M2 5l10 8 10-8" fill="none" stroke="var(--mid-blue)" stroke-width="2"/></svg>
        <span>www.marrowbyferryline.com</span>
      </li>
    </ul>

    <div class="wordmark">
      <span class="name">MARROWBY</span>
      <span class="tagline">Water Taxi &amp; Transport</span>
    </div>

    <svg class="base-bands" width="660" height="130" viewBox="0 0 660 130" aria-hidden="true">
      <polygon points="0,10 0,48 280,130 300,130 300,112" fill="var(--navy)"/>
      <polygon points="0,18 280,118" fill="none"/>
      <polygon points="300,112 340,92 660,130 300,130" fill="var(--sky)"/>
      <polygon points="0,0 8,0 0,10" fill="var(--navy)"/>
    </svg>
  </section>

</body>
</html>
```